we need a design for Water Bottle Lable Wrap
The product is called Calmora Springs is a restructured water. its a very healthy and rejuvenating water
we were looking at using as a tag ling Restore, Recover, Rejuvenate.

```html
<!DOCTYPE html>
<html lang="en">
<head>
<meta charset="utf-8">
<title>Calmora Springs – Bottle Label Wrap</title>
<link rel="stylesheet" href="https://fonts.googleapis.com/css2?family=Montserrat:wght@500;600;800&display=swap">
<style>
  :root {
    --page-bg: #f2f3f4;
    --sky: #d6ecf5;
    --surface: #8fd0ea;
    --water-mid: #2f93c6;
    --water-deep: #0f5784;
    --shallows: #a8d7d2;
    --sand: #efe0c8;
    --sand-warm: #d98b6c;
    --white: #ffffff;
    --accent-blue: #2b93c9;
    --list-blue: #1c6db3;
  }
  * { margin: 0; padding: 0; box-sizing: border-box; }
  html, body {
    width: 1200px;
    height: 1138px;
    overflow: hidden;
    background: var(--page-bg);
    font-family: "Montserrat", Arial, sans-serif;
  }
  .label {
    position: absolute;
    left: 102px;
    top: 34px;
    width: 996px;
    height: 1070px;
    overflow: hidden;
  }
  .label__scene {
    position: absolute;
    inset: 0;
    background: linear-gradient(
      to bottom,
      var(--sky) 0%,
      #c3e4f1 18%,
      var(--surface) 24%,
      var(--water-mid) 38%,
      #1d76a8 55%,
      var(--water-deep) 66%,
      #4a9aa8 74%,
      var(--shallows) 81%,
      var(--sand) 90%,
      var(--sand-warm) 100%
    );
  }
  .brand {
    position: absolute;
    left: 0;
    right: 0;
    top: 505px;
    text-align: center;
    color: var(--white);
    line-height: 1;
  }
  .brand__first {
    display: block;
    font-weight: 500;
    font-size: 108px;
    letter-spacing: 1px;
  }
  .brand__second {
    display: block;
    margin-top: 14px;
    font-weight: 800;
    font-size: 110px;
  }
  .descriptor {
    position: absolute;
    left: 214px;
    top: 756px;
    width: 568px;
    height: 71px;
    background: var(--white);
    border-radius: 0 30px 0 30px;
    color: var(--accent-blue);
    font-weight: 600;
    font-size: 35px;
    line-height: 71px;
    text-align: center;
    letter-spacing: 0.5px;
  }
  .benefits {
    position: absolute;
    left: 336px;
    top: 852px;
    list-style: none;
    color: var(--list-blue);
    font-weight: 600;
    font-size: 40px;
    line-height: 50px;
  }
  .benefits li {
    display: flex;
    align-items: center;
    gap: 14px;
  }
  .benefits svg { width: 34px; height: 34px; flex: none; }
</style>
</head>
<body>
  <main class="label">
    <div class="label__scene" role="img" aria-label="Underwater scene: light sky above a wavy water surface with bubbles, sun rays into deep blue water, fading to a sandy sea floor"></div>

    <h1 class="brand">
      <span class="brand__first">CALMORA</span>
      <span class="brand__second">SPRINGS</span>
    </h1>

    <p class="descriptor">RESTRUCTURED WATER</p>

    <ul class="benefits">
      <li><svg viewBox="0 0 34 34" aria-hidden="true"><polyline points="4,18 13,27 30,7" fill="none" stroke="currentColor" stroke-width="5" stroke-linecap="round" stroke-linejoin="round"/></svg>RESTORE</li>
      <li><svg viewBox="0 0 34 34" aria-hidden="true"><polyline points="4,18 13,27 30,7" fill="none" stroke="currentColor" stroke-width="5" stroke-linecap="round" stroke-linejoin="round"/></svg>RECOVER</li>
      <li><svg viewBox="0 0 34 34" aria-hidden="true"><polyline points="4,18 13,27 30,7" fill="none" stroke="currentColor" stroke-width="5" stroke-linecap="round" stroke-linejoin="round"/></svg>REJUVENATE</li>
    </ul>
  </main>
</body>
</html>
```